Im want a website LIKE VRX's and FleetHollow.com's with product payment options like Trenzo's

I need a website LIKE VRX with a header made EXACTLY LIKE THAT OF FLEETHOLLOWS .

The front page photo should be like that of FLEETHOLLOW's webpage as well.

The name of the website will be called "M.K. (Caldera Key)".

We will be targeting ALL MARKETS in a small town in central Panama and charging businesses "listing fees" like a phone book does but also providing informational blogs, news, and other interesting activities.

THIS IS A MULTI PAGE WEBSITE

THIS IS WHERE VRX's website meets Brivelle/FleetHollow.

Once the layout is built I will tweak and modify, add information, and upload items for sale.

Here is a list of specific categories that should be listed out above the front page header image/search bar

-- Home -- News -- Travel -- Activities -- Shop & Dine -- Store -- More... --

These categories should be spread across the bottom of the page in three sections:

WHATS SO GREAT ABOUT (Caldera Key),
HAND PICKED TOURS
ACTIVITIES etc.

Also lets use www.Trenzo.example 's
"HOT DESTINATIONS"
"BEAT THE BEST PRICES IN BOQUETE"
"OCTOBERS INSIDER PICKS"
"TOP DESTINATIONS"
and spread them in four sections side-by-side near the bottom of the page.

Overall I would like to see the finished product to be something LIKE VRX's and FleetHollows.

WE NEED ONLINE PAYMENT OPTIONS LIKE BRIVELLE'S WEBSITE HAS

This will be a desktop website but should be very mobile friendly as well.

-rodmund

P.S. Good luck!

If it isn't already too late to change the website name, the name of the website should be "Caldera Key". Added Friday, October 9, 2015

What do you guys think the budget should be to win this? Added Saturday, October 10, 2015

www.palmorra.example is the most amazing simple site. Whoever can make me a replica with my specifications will win immediately!!!! Added Sunday, October 18, 2015

OMG www.palmorra.example is the bomb!So simple and elegant. Whoever can make me an EXACT REPLICA OF WWW.PALMORRA.EXAMPLE as my site with the specifications mentioned in my brief will take home the $825.00 immediately! Good luck amigos! Added Sunday, October 18, 2015

Does anybody know how to add recurring monthly billing options on this website? Added Sunday, October 18, 2015

ALL MARKETS

Product

Coded - Design and coding required

5+ page

• Coinvey payment options.
• I must be able to add and remove photos/text and video from the HTML files in the page.
• Be creative my friends, and may the odds be forever in your favor!
• I added some photos of a good layout for our page below.

```html
<!DOCTYPE html>
<html lang="en">
<head>
<meta charset="utf-8">
<title>Caldera Key</title>
<link href="https://fonts.googleapis.com/css2?family=Open+Sans:ital,wght@0,400;0,600;0,700;0,800;1,400;1,600&display=swap" rel="stylesheet">
<style>
:root{
  --accent:#1ea0d8;
  --accent-dark:#1584b4;
  --ink:#333;
  --muted:#8a8a8a;
  --soft:#ededed;
  --line:#dcdcdc;
  --date:#d9412f;
  --star:#f2b01e;
  --footer:#2e2e2e;
  --footer-deep:#222;
  --white:#fff;
}
*{box-sizing:border-box;margin:0;padding:0}
html,body{width:1200px;height:2292px;overflow:hidden}
body{font-family:"Open Sans",Arial,sans-serif;color:var(--ink);background:var(--white);position:relative}
.topbar{height:40px;display:flex;justify-content:flex-end;align-items:center;gap:20px;padding-right:110px;font-size:11px;color:var(--muted)}
.hero{position:relative;height:700px;margin:0 24px;border-radius:4px;overflow:hidden;box-shadow:0 6px 18px rgba(0,0,0,.25)}
.hero-photo{position:absolute;inset:0;background:
  radial-gradient(ellipse at 75% 45%,rgba(230,240,240,.9) 0,rgba(200,220,225,.4) 12%,transparent 28%),
  linear-gradient(180deg,#2e5a2a 0%,#4d7b3a 30%,#6f8f55 55%,#3f6a3a 75%,#6c7f4a 100%);}
.hero-photo::before{content:"";position:absolute;left:0;top:0;bottom:0;width:22%;background:linear-gradient(90deg,#7fc7d8,#b8dfe0 70%,transparent)}
.header{position:absolute;top:0;left:0;right:0;height:110px;display:flex;align-items:center;justify-content:space-between;padding:0 60px 0 50px;background:linear-gradient(180deg,rgba(0,0,0,.35),transparent)}
.brand{display:flex;align-items:center;gap:10px;color:var(--white);font-weight:800;font-size:22px;line-height:1}
.brand-mark{width:34px;height:34px;border-radius:50%;background:var(--accent)}
.nav{display:flex;gap:6px;list-style:none}
.nav li{font-size:11px;font-weight:600;color:var(--white);padding:8px 14px;letter-spacing:.3px}
.nav li.active{border-bottom:2px solid var(--white)}
.hero-caption{position:absolute;left:0;right:0;top:300px;text-align:center;color:var(--white)}
.hero-caption h1{font-size:54px;font-weight:800;letter-spacing:1px;text-shadow:0 2px 6px rgba(0,0,0,.4)}
.hero-caption p{margin-top:12px;font-size:30px;font-style:italic;line-height:42px;text-shadow:0 2px 6px rgba(0,0,0,.4)}
.hero-arrow{position:absolute;top:390px;width:30px;height:30px}
.hero-arrow.prev{left:20px}.hero-arrow.next{right:20px}
.section-title{text-align:center;color:var(--accent);font-size:19px;font-weight:600;letter-spacing:.5px}
.welcome{padding:44px 100px 0;height:212px}
.welcome p{margin-top:20px;font-size:12px;line-height:20px;color:var(--muted);text-align:center}
.read-more{display:block;text-align:right;font-size:11px;color:var(--accent);margin-top:12px}
.services{background:var(--soft);height:428px;padding:60px 100px 0}
.service-row{display:flex;gap:40px;margin-top:50px}
.service{flex:1}
.service-head{display:flex;align-items:center;gap:14px}
.service-icon{width:60px;height:60px;border-radius:50%;border:2px solid #bbb;display:flex;align-items:center;justify-content:center;flex:none}
.service h3{font-size:13px;font-weight:700;color:#444}
.service h4{font-size:11px;font-style:italic;color:var(--accent);font-weight:600;margin-top:4px}
.service p{font-size:11px;line-height:18px;color:var(--muted);margin-top:16px}
.service .read-more{text-align:left}
.popular{padding:34px 100px 0}
.popular h2{font-size:16px;font-weight:700;color:var(--accent)}
.visit{display:flex;gap:24px;height:150px;margin-top:26px;align-items:flex-start;border-bottom:1px solid var(--line);padding-bottom:20px}
.visit-photo{width:200px;height:128px;flex:none;border-radius:2px}
.visit-body{flex:1}
.visit h3{font-size:13px;font-weight:700;color:#333}
.visit .date{font-size:10px;color:var(--date);margin-top:4px}
.visit p{font-size:10.5px;line-height:16px;color:var(--muted);margin-top:8px}
.stars{color:var(--star);font-size:12px;margin-top:6px;letter-spacing:1px}
.visit-price{width:140px;text-align:right;padding-top:10px}
.visit-price small{font-size:10px;color:var(--accent)}
.visit-price strong{display:block;font-size:22px;font-weight:600;color:#333;margin-top:4px}
.btn{display:inline-block;background:var(--accent);color:var(--white);font-size:10px;font-weight:700;padding:8px 14px;margin-top:12px;border-radius:2px}
.footer{position:absolute;left:0;right:0;top:1990px;height:270px;background:var(--footer);color:#bbb;padding:30px 100px 0;display:flex;gap:60px}
.footer h4{color:var(--white);font-size:12px;font-weight:600;letter-spacing:.5px;margin-bottom:18px}
.footer-col{flex:1;font-size:10.5px;line-height:17px}
.contact-line{display:flex;gap:10px;margin-bottom:14px;align-items:flex-start}
.contact-line svg{flex:none}
.news-item{display:flex;gap:10px;margin-bottom:16px}
.news-thumb{width:60px;height:46px;flex:none}
.field{height:26px;background:var(--white);margin-bottom:10px;width:200px}
.newsletter .btn{margin-top:2px}
.social-line{display:flex;align-items:center;gap:10px;margin-bottom:14px}
.social-line span.sq{width:18px;height:18px;background:#555;flex:none}
.bottom-bar{position:absolute;left:0;right:0;top:2260px;height:32px;background:var(--footer-deep);color:#777;font-size:10px;display:flex;align-items:center;justify-content:center}
</style>
</head>
<body>
<div class="topbar"><span>SIGN IN | REGISTER</span><span>LANGUAGE ▾</span></div>

<section class="hero">
  <div class="hero-photo" role="img" aria-label="Tropical waterfall over mossy rocks in a green forest, with a turquoise beach at the left"></div>
  <header class="header">
    <div class="brand"><span class="brand-mark"></span>CALDERA KEY</div>
    <ul class="nav">
      <li class="active">HOME</li><li>ABOUT US</li><li>OUR SERVICES ▾</li><li>WHAT VISIT ▾</li><li>BOOK NOW</li><li>CONTACT US</li>
    </ul>
  </header>
  <div class="hero-caption">
    <h1>CALDERA KEY</h1>
    <p>Cu vix lorem augue graeci, facete probatus ut ius.<br>Unum utinam ceteros ut, te sed</p>
  </div>
  <svg class="hero-arrow prev" viewBox="0 0 30 30"><path d="M19 6 10 15l9 9" fill="none" stroke="#fff" stroke-width="3"/></svg>
  <svg class="hero-arrow next" viewBox="0 0 30 30"><path d="M11 6l9 9-9 9" fill="none" stroke="#fff" stroke-width="3"/></svg>
</section>

<section class="welcome">
  <h2 class="section-title">WELCOME TO CALDERA KEY</h2>
  <p>Lorem ipsum dolor sit amet, consectetur adipiscing elit, sed do eiusmod tempor incididunt ut labore et dolore magna aliqua. Ut enim ad minim veniam, quis nostrud exercitation ullamco laboris nisi ut aliquip ex ea commodo consequat. Duis aute irure dolor in reprehenderit in voluptate velit esse cillum dolore eu fugiat nulla pariatur. Excepteur sint occaecat cupidatat non proident, sunt in culpa qui officia deserunt mollit anim id est laborum sed ut perspiciatis.</p>
  <span class="read-more">Read More »</span>
</section>

<section class="services">
  <h2 class="section-title">OUR SERVICES</h2>
  <div class="service-row">
    <div class="service">
      <div class="service-head">
        <span class="service-icon"><svg width="28" height="28" viewBox="0 0 28 28"><circle cx="14" cy="14" r="11" fill="none" stroke="#888" stroke-width="2"/><path d="M14 6v8l5 4" fill="none" stroke="#888" stroke-width="2"/></svg></span>
        <div><h3>SELLING GUIDED TOURS</h3><h4>Nihil Servan Aliquando Sea</h4></div>
      </div>
      <p>Ex mel hendrerit accumsan, vel at modus sententiae mel, quas vivendo aliquam nam no. Ei nostrum moderatius per, in mazim eleifend sit. Vis te putent mentitum ea.</p>
      <span class="read-more">Read More »</span>
    </div>
    <div class="service">
      <div class="service-head">
        <span class="service-icon"><svg width="28" height="28" viewBox="0 0 28 28"><rect x="6" y="5" width="16" height="19" fill="none" stroke="#888" stroke-width="2"/><path d="M10 9h2M16 9h2M10 14h2M16 14h2M12 24v-5h4v5" stroke="#888" stroke-width="2" fill="none"/></svg></span>
        <div><h3>HOTEL FACILITIES</h3><h4>Nihil Servan Aliquando Sea</h4></div>
      </div>
      <p>Ex mel hendrerit accumsan, vel at modus sententiae mel, quas vivendo aliquam nam no. Ei nostrum moderatius per, in mazim eleifend sit. Vis te putent mentitum ea.</p>
      <span class="read-more">Read More »</span>
    </div>
    <div class="service">
      <div class="service-head">
        <span class="service-icon"><svg width="28" height="28" viewBox="0 0 28 28"><path d="M4 18l3-7h14l3 7v4H4z" fill="none" stroke="#888" stroke-width="2"/><circle cx="9" cy="22" r="2" fill="#888"/><circle cx="19" cy="22" r="2" fill="#888"/></svg></span>
        <div><h3>RENTAL VEHICLES</h3><h4>Nihil Servan Aliquando Sea</h4></div>
      </div>
      <p>Ex mel hendrerit accumsan, vel at modus sententiae mel, quas vivendo aliquam nam no. Ei nostrum moderatius per, in mazim eleifend sit. Vis te putent mentitum ea.</p>
      <span class="read-more">Read More »</span>
    </div>
  </div>
</section>

<section class="popular">
  <h2>MOST POPULAR VISITINGS</h2>
  <article class="visit">
    <div class="visit-photo" role="img" aria-label="Colourful tropical bird perched among green leaves" style="background:linear-gradient(135deg,#3f7a2e,#c8412a 55%,#6a9a3a)"></div>
    <div class="visit-body">
      <h3>EU ORREM REPRIMIQUE NULLAM VIS HEL GILIGS IRURE FALLI ERMOD INCIDERINT.</h3>
      <div class="date">october 18, 2015</div>
      <p>Ne dolorege torquatos fabellas mea, cu per quando offendit placerat, nec an ludus ermod lucilianus. Ex dolorege torquatos fabellas mea, cu est quando placerat ludus ermod. Pro cu quando offendit placerat, nec ut ludus ermod incidunt.</p>
      <div class="stars">★★★★★</div>
    </div>
    <div class="visit-price"><small>Per Day</small><strong>$ 54.00</strong><span class="btn">VIEW DETAILS</span></div>
  </article>
  <article class="visit">
    <div class="visit-photo" role="img" aria-label="Ornate church interior with golden altar" style="background:linear-gradient(135deg,#6b4a30,#c79a5a 50%,#8a6a4a)"></div>
    <div class="visit-body">
      <h3>EU ORREM REPRIMIQUE NULLAM VIS HEL GILIGS IRURE FALLI ERMOD INCIDERINT.</h3>
      <div class="date">october 18, 2015</div>
      <p>Ne dolorege torquatos fabellas mea, cu per quando offendit placerat, nec an ludus ermod lucilianus. Ex dolorege torquatos fabellas mea, cu est quando placerat ludus ermod. Pro cu quando offendit placerat, nec ut ludus ermod incidunt.</p>
      <div class="stars">★★★★★</div>
    </div>
    <div class="visit-price"><small>Per Day</small><strong>$ 54.00</strong><span class="btn">VIEW DETAILS</span></div>
  </article>
  <article class="visit">
    <div class="visit-photo" role="img" aria-label="Old stone ruins under a blue sky" style="background:linear-gradient(180deg,#6f9fd0,#9aa088 55%,#5a5a48)"></div>
    <div class="visit-body">
      <h3>EU ORREM REPRIMIQUE NULLAM VIS HEL GILIGS IRURE FALLI ERMOD INCIDERINT.</h3>
      <div class="date">october 18, 2015</div>
      <p>Ne dolorege torquatos fabellas mea, cu per quando offendit placerat, nec an ludus ermod lucilianus. Ex dolorege torquatos fabellas mea, cu est quando placerat ludus ermod. Pro cu quando offendit placerat, nec ut ludus ermod incidunt.</p>
      <div class="stars">★★★★★</div>
    </div>
    <div class="visit-price"><small>Per Day</small><strong>$ 54.00</strong><span class="btn">VIEW DETAILS</span></div>
  </article>
</section>

<footer class="footer">
  <div class="footer-col">
    <h4>CONTACT US</h4>
    <div class="contact-line"><svg width="14" height="16" viewBox="0 0 14 16"><path d="M7 1a5 5 0 0 0-5 5c0 4 5 9 5 9s5-5 5-9a5 5 0 0 0-5-5z" fill="#999"/></svg><span>14 Calle Sendero, Valle Alto,<br>Chiriquí 0427</span></div>
    <div class="contact-line"><svg width="14" height="12" viewBox="0 0 14 12"><rect x="1" y="1" width="12" height="10" fill="none" stroke="#999" stroke-width="1.5"/><path d="M1 1l6 5 6-5" fill="none" stroke="#999" stroke-width="1.5"/></svg><span>hello@calderakey.example</span></div>
    <div class="contact-line"><svg width="14" height="14" viewBox="0 0 14 14"><path d="M3 1l3 3-2 2a8 8 0 0 0 4 4l2-2 3 3-2 2C6 13 1 8 1 3z" fill="#999"/></svg><span>+507 555 0142 / +507 555 0187</span></div>
  </div>
  <div class="footer-col">
    <h4>NEWS EVENTS</h4>
    <div class="news-item"><div class="news-thumb" role="img" aria-label="Green hillside scene" style="background:linear-gradient(135deg,#4c7a3a,#9ab870)"></div><span>LOREM IPSUM<br>Sed ut perspiciatis unde omnis iste natus error.</span></div>
    <div class="news-item"><div class="news-thumb" role="img" aria-label="Coastal bay scene" style="background:linear-gradient(135deg,#3d86b0,#a8d0d8)"></div><span>LOREM IPSUM<br>Sed ut perspiciatis unde omnis iste natus error.</span></div>
  </div>
  <div class="footer-col newsletter">
    <h4>NEWS LETTER</h4>
    <div class="field"></div>
    <div class="field"></div>
    <span class="btn">SUBSCRIBE</span>
  </div>
  <div class="footer-col">
    <h4>SOCIAL MEDIA</h4>
    <div class="social-line"><span class="sq"></span>Community</div>
    <div class="social-line"><span class="sq"></span>Updates</div>
    <div class="social-line"><span class="sq"></span>Network</div>
    <div class="social-line"><span class="sq"></span>Circle</div>
  </div>
</footer>
<div class="bottom-bar">Copyright © 2015 Caldera Key. All rights reserved.</div>
</body>
</html>
```